Birchline Septic Solutions

Would like to see some single sided ones but would also like to see some double sided with one sided only being the logo. Owners name is Colin Vandro. Phone number is 555-214-0387
Services are pumping, inspections, installs, and repairs

Contact Information for Business Card

555-241-0387 Colin Vandro Fernbrook, IA

```html
<!DOCTYPE html>
<html lang="en">
<head>
<meta charset="utf-8">
<title>Birchline Septic Solutions – Business Cards</title>
<link rel="stylesheet" href="https://fonts.googleapis.com/css2?family=Open+Sans:wght@400;600;700;800&display=swap">
<style>
  :root {
    --page-bg: #232323;
    --card-dark: #222226;
    --teal: #23bdb6;
    --teal-deep: #179a94;
    --teal-light: #5fd6c4;
    --white: #ffffff;
    --ink: #141418;
  }
  * { box-sizing: border-box; margin: 0; padding: 0; }
  html, body { width: 1200px; height: 779px; overflow: hidden; background: var(--page-bg); }
  body { font-family: "Open Sans", Arial, sans-serif; position: relative; }

  .card {
    position: absolute;
    top: 112px;
    width: 310px;
    height: 555px;
    border-radius: 22px;
    overflow: hidden;
  }

  /* Logo side */
  .card--logo { left: 225px; background: var(--teal); }
  .card--logo .pattern-field {
    position: absolute; inset: 0;
    background: linear-gradient(160deg, var(--teal-light) 0%, var(--teal) 45%, var(--teal-deep) 100%);
  }
  .card--logo .brand-mark {
    position: absolute;
    top: 70px; left: 0; right: 0;
    text-align: center;
    color: var(--ink);
    font-weight: 800;
    font-size: 15px;
    letter-spacing: 0.5px;
    line-height: 1.25;
  }

  /* Contact side */
  .card--contact { left: 665px; background: var(--card-dark); }
  .card--contact .brand-name {
    position: absolute;
    top: 62px; left: 0; right: 0;
    text-align: center;
    color: var(--white);
    font-weight: 800;
    font-size: 27px;
    line-height: 1.15;
    letter-spacing: 0.5px;
  }
  .owner {
    position: absolute;
    top: 236px; left: 0; right: 0;
    text-align: center;
  }
  .owner__name { font-size: 25px; font-weight: 700; color: var(--white); line-height: 1.1; }
  .owner__first { color: var(--teal); }
  .owner__town { font-size: 14px; font-weight: 600; color: var(--white); margin-top: 2px; }

  .contact-graphic { position: absolute; top: 300px; left: 0; width: 310px; height: 125px; }

  .phone {
    position: absolute;
    top: 348px; left: 0; right: 0;
    text-align: center;
    color: var(--white);
    font-size: 21px;
    font-weight: 600;
    letter-spacing: 0.5px;
  }
  .services-pill {
    position: absolute;
    top: 394px; left: 50%;
    transform: translateX(-50%);
    height: 20px;
    line-height: 14px;
    background: var(--teal);
    color: var(--white);
    font-size: 12px;
    font-weight: 700;
    padding: 3px 18px;
    border-radius: 50%;
    letter-spacing: 0.5px;
  }
  .services-list {
    position: absolute;
    top: 432px; left: 0; right: 0;
    list-style: none;
    text-align: center;
    color: var(--white);
    font-size: 14px;
    line-height: 1.4;
  }
</style>
</head>
<body>

  <section class="card card--logo">
    <div class="pattern-field" role="img" aria-label="Repeating mountain and pine tree pattern in light and deep teal"></div>
    <div class="brand-mark">Birchline<br>Septic Solutions</div>
  </section>

  <section class="card card--contact">
    <div class="brand-name">Birchline<br>Septic Solutions</div>

    <div class="owner">
      <div class="owner__name"><span class="owner__first">Colin</span> Vandro</div>
      <div class="owner__town">Fernbrook, IA</div>
    </div>

    <svg class="contact-graphic" viewBox="0 0 310 125" aria-hidden="true">
      <g fill="#23bdb6">
        <circle cx="12" cy="14" r="2"/><circle cx="26" cy="14" r="2.5"/><circle cx="42" cy="14" r="3"/>
        <circle cx="60" cy="14" r="3.5"/><circle cx="80" cy="14" r="4.5"/><circle cx="102" cy="14" r="5.5"/>
        <circle cx="125" cy="14" r="6"/>
        <circle cx="185" cy="14" r="6"/><circle cx="208" cy="14" r="5.5"/><circle cx="230" cy="14" r="4.5"/>
        <circle cx="250" cy="14" r="3.5"/><circle cx="268" cy="14" r="3"/><circle cx="284" cy="14" r="2.5"/>
        <circle cx="298" cy="14" r="2"/>
        <circle cx="155" cy="14" r="11"/>
        <path d="M151 9c1-1 2-1 2.5 0l1 2c.3.6 0 1-.4 1.4l-.6.5c.6 1.3 1.6 2.3 2.9 2.9l.5-.6c.4-.4.8-.7 1.4-.4l2 1c1 .5 1 1.5 0 2.5-1 1-2.5 1.2-4 .5-3-1.4-5.3-3.7-6.7-6.7-.7-1.5-.5-3 .5-4z" fill="#ffffff"/>
        <path d="M150 26l5 7 5-7z"/>
        <circle cx="12" cy="104" r="2"/><circle cx="26" cy="104" r="2.5"/><circle cx="42" cy="104" r="3"/>
        <circle cx="60" cy="104" r="3.5"/><circle cx="80" cy="104" r="4.5"/><circle cx="100" cy="104" r="5.5"/>
        <circle cx="210" cy="104" r="5.5"/><circle cx="230" cy="104" r="4.5"/>
        <circle cx="250" cy="104" r="3.5"/><circle cx="268" cy="104" r="3"/><circle cx="284" cy="104" r="2.5"/>
        <circle cx="298" cy="104" r="2"/>
        <path d="M150 114l5 6 5-6z"/>
      </g>
    </svg>

    <div class="phone">555-241-0387</div>
    <div class="services-pill">SERVICES</div>
    <ul class="services-list">
      <li>Installs</li>
      <li>Pumping</li>
      <li>Inspections</li>
      <li>And Repairs</li>
    </ul>
  </section>

</body>
</html>
```